Patent Law

Need to develop a home page for a patent lawyer.

Colors should go with logo, blues...

Company Name- Velun Tresk, PLLC

Company Overview-

I am an Intellectual Property Lawyer and focus on patents, copyrights, trademarks, & trade secrets. I work with small businesses and start ups in the chemical and biotech industries.

Why Us-

I am small firm that can provide large-firm service at a reasonable price. I also can charge flat-fees for entreprenuers in certain practice areas.

Services-
Intellectual Property
Patents
Copyrights
Trademarks
Trade secrets
Healthcare Compliance
Elder law
Wills
Trusts

Website we like-
http://www.quorvantlegal.example/ - within industry!!
http://www.daltrowemiko.example/
http://ulbrixtane.example/
http://thegravelcounsel.example/

Target Market(s)

My customers will be small business, specifically small start-up companies in the chemical and biotech arena.

Industry/Entity Type

Trade

Requirements
Must have
• Colors should go with logo, blues...

```html
<!DOCTYPE html>
<html lang="en">
<head>
<meta charset="utf-8">
<title>Velun Tresk, PLLC — Patent &amp; Intellectual Property Law</title>
<link href="https://fonts.googleapis.com/css2?family=Lato:wght@400;700&display=swap" rel="stylesheet">
<style>
:root{
  --bar-dark:#262626;
  --bar-mid:#454545;
  --nav-text:#e6e6e6;
  --accent-cyan:#52d3e8;
  --teal-base:#6cc6c9;
  --teal-light:#b8f6f8;
  --teal-deep:#58b4b8;
  --ink:#173b42;
  --body-ink:#1f4a4c;
  --button-blue:#2f3d8e;
  --button-blue-light:#4a5bb8;
  --card-top:#d5fbfb;
  --card-bottom:#9ee3e3;
}
*{margin:0;padding:0;box-sizing:border-box}
html,body{width:1200px;height:1155px;overflow:hidden}
body{
  position:relative;
  font-family:Arial, Helvetica, sans-serif;
  background:
    radial-gradient(ellipse 560px 420px at 600px 60px, var(--teal-light) 0%, rgba(184,246,248,0) 100%),
    linear-gradient(180deg,#8fe3e6 0%, var(--teal-base) 40%, var(--teal-deep) 100%);
}
.top-bar{
  position:absolute;left:0;top:0;width:1200px;height:36px;
  background:linear-gradient(180deg,var(--bar-mid),var(--bar-dark));
  font-family:'Lato',sans-serif;font-size:13px;color:var(--nav-text);
}
.main-nav{position:absolute;left:180px;top:0;height:36px;display:flex}
.main-nav a{
  display:block;height:36px;line-height:34px;padding:0 15px;color:var(--nav-text);
  text-decoration:none;border-right:1px solid #3a3a3a;box-shadow:1px 0 0 #555;
}
.main-nav a:last-child{border-right:none;box-shadow:none}
.main-nav a.is-active{
  height:43px;padding:0 7px;
  background:linear-gradient(180deg,#3fa8b5,#1c7a88);
  border-radius:0 0 4px 4px;color:#fff;
  box-shadow:0 2px 3px rgba(0,0,0,.35);
}
.contact-strip{
  position:absolute;left:787px;top:8px;display:flex;align-items:center;gap:6px;
  color:var(--accent-cyan);font-size:14px;letter-spacing:.3px;
}
.contact-strip svg{display:block}

.brand{position:absolute;left:0;top:62px;width:1200px;text-align:center}
.brand-dot{width:44px;height:44px;border-radius:50%;background:#1f4f9a;margin:0 auto 16px}
.brand-name{font-family:'Lato',sans-serif;font-weight:400;font-size:15px;letter-spacing:1.2px;color:#1b3346;text-transform:uppercase}

.slider{position:absolute;left:0;top:160px}

.divider{position:absolute;left:0;top:555px}

.feature-card{
  position:absolute;top:600px;width:263px;height:165px;border-radius:10px;
  background:linear-gradient(180deg,var(--card-top),var(--card-bottom));
  border:2px solid rgba(255,255,255,.85);
  box-shadow:0 3px 8px rgba(0,80,90,.25);
}
.feature-card h2{
  margin:9px 13px 0;padding-bottom:3px;
  font-family:'Lato',sans-serif;font-weight:400;font-size:15px;color:var(--ink);
  border-bottom:1px solid #7fb9bb;
}
.feature-card p{margin:14px 14px 0 15px;font-size:11.5px;line-height:15.2px;color:var(--body-ink)}
.pill-button{
  position:absolute;right:19px;bottom:17px;height:20px;padding:0 6px;border-radius:10px;
  background:linear-gradient(180deg,var(--button-blue-light),var(--button-blue));
  color:#fff;font-size:10px;line-height:20px;border:1px solid #c8e8ff;
}
.card-why{left:174px}
.card-what{left:468px}
.card-contact{left:758px}

.welcome{position:absolute;left:165px;top:820px;width:604px}
.welcome h1{
  display:inline-block;font-family:'Lato',sans-serif;font-weight:400;font-size:27px;
  color:var(--ink);letter-spacing:-.2px;padding-bottom:2px;border-bottom:2px dotted #e6ffff;
}
.welcome p{margin:14px 0 0 3px;font-size:11.5px;line-height:15.2px;color:var(--body-ink)}
.welcome p + p{margin-top:15px}

.subscribe{
  position:absolute;left:780px;top:815px;width:252px;height:175px;border-radius:6px;
  background:linear-gradient(180deg,#bff7f6,#96e6e2);
  box-shadow:0 3px 8px rgba(0,60,70,.3);overflow:hidden;
}
.subscribe h3{
  height:37px;line-height:38px;text-align:center;font-weight:400;font-size:17px;color:#fff;
  background:linear-gradient(180deg,#4b5ec0,#2d3b95);border-bottom:2px solid #e0ffff;
}
.field{position:absolute;left:8px;display:flex;align-items:center;font-size:11.5px;color:#2b4a4c}
.field span{width:38px}
.field i{display:block;width:196px;height:27px;background:#fff;border:1px solid #d4eeee}
.field-name{top:56px}
.field-email{top:101px}
.subscribe .pill-button{right:10px;bottom:12px;font-size:11.5px;height:21px;line-height:20px}

.footer{position:absolute;left:0;top:1040px}
.copyright{position:absolute;left:180px;top:1108px;font-size:11px;color:#333}
.social{position:absolute;left:922px;top:1102px;display:flex;gap:11px}
.social span{width:28px;height:28px;border-radius:3px;display:block}
.social .s-one{background:linear-gradient(180deg,#3d6fc4,#234e98)}
.social .s-two{background:linear-gradient(180deg,#45c0e0,#1a8fb4)}
.social .s-three{background:linear-gradient(180deg,#f59a45,#d8611d)}
</style>
</head>
<body>

<header class="top-bar">
  <nav class="main-nav">
    <a class="is-active">Homepage</a>
    <a>About Velun</a>
    <a>Practice Area</a>
    <a>Lawyers</a>
    <a>Case Study</a>
    <a>Contact Us</a>
  </nav>
  <div class="contact-strip">
    <svg width="10" height="15" viewBox="0 0 10 15"><path d="M5 0a5 5 0 0 1 5 5c0 3.5-5 10-5 10S0 8.5 0 5a5 5 0 0 1 5-5z" fill="#52d3e8"/><circle cx="5" cy="5" r="1.8" fill="#2e2e2e"/></svg>
    <span>Our Map Location</span>
    <svg width="20" height="20" viewBox="0 0 20 20"><circle cx="10" cy="10" r="8.8" fill="none" stroke="#52d3e8" stroke-width="1.6"/><path d="M7 5.5l1.6-.4 1 2.4-1.1.9a6 6 0 0 0 2.7 2.8l.9-1.1 2.4 1-.4 1.6c-3.6.4-7.6-3.6-7.1-7.2z" fill="#52d3e8"/></svg>
    <span>123 555 0148</span>
  </div>
</header>

<div class="brand">
  <div class="brand-dot"></div>
  <div class="brand-name">Velun Tresk, PLLC</div>
</div>

<svg class="slider" width="1200" height="375" viewBox="0 160 1200 375">
  <defs>
    <linearGradient id="ring" x1="0" y1="0" x2="0" y2="1">
      <stop offset="0" stop-color="#f4f4f4"/><stop offset=".5" stop-color="#8c8c8c"/><stop offset="1" stop-color="#e6e6e6"/>
    </linearGradient>
    <linearGradient id="photoCenter" x1="0" y1="0" x2="1" y2="1">
      <stop offset="0" stop-color="#c8d6df"/><stop offset=".5" stop-color="#6b6a6c"/><stop offset="1" stop-color="#2f2f33"/>
    </linearGradient>
    <linearGradient id="photoSide" x1="0" y1="0" x2="1" y2="1">
      <stop offset="0" stop-color="#d9e2e8"/><stop offset=".55" stop-color="#9aa4ad"/><stop offset="1" stop-color="#2c3036"/>
    </linearGradient>
    <radialGradient id="shadow"><stop offset="0" stop-color="#2e7f84" stop-opacity=".45"/><stop offset="1" stop-color="#2e7f84" stop-opacity="0"/></radialGradient>
  </defs>
  <path d="M165 225 Q190 280 225 300" fill="none" stroke="#d8ffff" stroke-width="2"/>
  <path d="M370 383 Q400 392 425 396" fill="none" stroke="#d8ffff" stroke-width="2"/>
  <path d="M752 400 Q790 392 822 382" fill="none" stroke="#d8ffff" stroke-width="2"/>
  <path d="M965 305 Q1010 280 1038 230" fill="none" stroke="#d8ffff" stroke-width="2"/>
  <path d="M165 200 L137 228 L165 256" fill="none" stroke="#1d5560" stroke-width="1.6"/>
  <path d="M1041 200 L1069 228 L1041 256" fill="none" stroke="#1d5560" stroke-width="1.6"/>
  <ellipse cx="295" cy="424" rx="75" ry="9" fill="url(#shadow)"/>
  <ellipse cx="892" cy="424" rx="75" ry="9" fill="url(#shadow)"/>
  <ellipse cx="588" cy="514" rx="150" ry="16" fill="url(#shadow)"/>
  <circle cx="295" cy="333" r="84" fill="url(#ring)"/>
  <circle cx="295" cy="333" r="78" fill="url(#photoSide)" role="img" aria-label="Photo: colleagues applauding in a bright office meeting"/>
  <circle cx="892" cy="333" r="84" fill="url(#ring)"/>
  <circle cx="892" cy="333" r="78" fill="url(#photoSide)" role="img" aria-label="Photo: two business professionals reviewing a document together"/>
  <circle cx="588" cy="343" r="174" fill="url(#ring)"/>
  <circle cx="588" cy="343" r="165" fill="url(#photoCenter)" role="img" aria-label="Photo: attorney in a suit in front of a team meeting at a conference table"/>
</svg>

<svg class="divider" width="1200" height="40" viewBox="0 555 1200 40">
  <path d="M100 591 Q600 540 1120 591 Q600 552 100 591z" fill="#d8ffff" opacity=".8"/>
</svg>

<section class="feature-card card-why">
  <h2>WHY US?</h2>
  <p>Lorem ipsum dolor sit amet, consectetuer adipiscing elit, sed diam nonummy nibh euismod tincidunt ut laoreet dolore magna aliquam erat volutpat. Ut wisi enim ad minim veniam, quis nostrud exerci...</p>
  <span class="pill-button">View more</span>
</section>
<section class="feature-card card-what">
  <h2>WHAT WE DO?</h2>
  <p>Lorem ipsum dolor sit amet, consectetuer adipiscing elit, sed diam nonummy nibh euismod tincidunt ut laoreet dolore magna aliquam erat volutpat. Ut wisi enim ad minim veniam, quis nostrud exerci...</p>
  <span class="pill-button">View more</span>
</section>
<section class="feature-card card-contact">
  <h2>CONTACT INFORMATION</h2>
  <p>Lorem ipsum dolor sit amet, consectetuer adipiscing elit, sed diam nonummy nibh euismod tincidunt ut laoreet dolore magna aliquam erat volutpat. Ut wisi enim ad minim veniam, quis nostrud exerci...</p>
  <span class="pill-button">View more</span>
</section>

<section class="welcome">
  <h1>WELCOME TO VELUN TRESK,PLL</h1>
  <p>Lorem ipsum dolor sit amet, consectetuer adipiscing elit, sed diam nonummy nibh euismod tincidunt ut laoreet dolore magna aliquam erat volutpat. Ut wisi enim ad minim veniam, quis nostrud exerci tation ullamcorper suscipit lobortis nisl ut aliquip ex ea commodo consequat. Duis autem vel eum iriure dolor in hendrerit in vulputate velit esse molestie consequat.</p>
  <p>Vel illum dolore eu feugiat nulla facilisis at vero eros et accumsan et iusto odio dignissim qui blandit praesent luptatum zzril delenit augue duis dolore te feugait nulla facilisi. Nam liber tempor cum soluta nobis eleifend option congue</p>
</section>

<aside class="subscribe">
  <h3>Subscribe Email</h3>
  <div class="field field-name"><span>Name:</span><i></i></div>
  <div class="field field-email"><span>Email:</span><i></i></div>
  <span class="pill-button">Subscribe</span>
</aside>

<svg class="footer" width="1200" height="115" viewBox="0 1040 1200 115">
  <defs><linearGradient id="foot" x1="0" y1="0" x2="0" y2="1"><stop offset="0" stop-color="#e9e9e9"/><stop offset=".3" stop-color="#f7f7f7"/><stop offset="1" stop-color="#ffffff"/></linearGradient></defs>
  <path d="M0 1074 Q600 1020 1200 1070 L1200 1155 L0 1155z" fill="url(#foot)"/>
  <path d="M0 1074 Q600 1020 1200 1070" fill="none" stroke="#ffffff" stroke-width="2"/>
</svg>
<p class="copyright">Copyrights 2014.VELUN TRESK,PLL, All Rights Reserved.</p>
<div class="social">
  <span class="s-one"></span><span class="s-two"></span><span class="s-three"></span>
</div>

</body>
</html>
```